Cutting Edge Property Services Provider is Looking to Update Business Card Design

We are looking to freshen up our business cards to match our cutting edge technology based image.

KORVANEX - Where Care Finds Its Pulse

More information about our company can be found on our website at www.korvanex-demo.net

We integrate technology in a historically low tech industry.

We have appeared on the Brisk 300/3000 list 2 years in a row and we're previously recognized as the 5th Quickest Rising Firm in San Diego.

Our core colors are blue and white, but are not against accents that might improve our image.

We currently have our Mission Statement on our Business Cards in a folding design:
KORVANEX IS THE LEADING BUILDING SERVICES INNOVATOR. BY COMBINING TECHNOLOGY WITH FUNCTIONAL TOOS THAT IMPROVE EFFICIENCY IN THE WORKPLACE, WE PROVIDE UNPARALLELED SERVICE IN THE INDUSTRY. DEVELOPING LASTING RELATIONSHIPS WITH OUR CLIENTS AND ASSOCIATES IS THE CORNERSTONE OF OUR SUCCESS.

We'd like to convey the image of a cutting edge, technology based company. Want the cards to pop.

Target Market(s)

Commercial Property Managers - 20 to 50 year old professionals

Industry/Entity Type

Business

Requirements
Must have
• Must utilize our logo obviously, but are definitely open to using variations on the logo. Utilizing the components of the logo, but maybe in different configurations or backgrounds, etc...

Must use the Name: KORVANEX.
Can also use KORVANEX PROPERTY SERVICES.

Must include the Mission Statement

Must say: Where Care Finds Its Pulse
Nice to have
• We are considering plastic stock, shaped cards, or folding cards.

Nothing over the top or really expensive, but will consider if it conveys innovation and technology.
Should not have
• No images of toilets, buildings, trees, or anything relating to commercial properties.

We want to convey our technology image.

```html
<!DOCTYPE html>
<html lang="en">
<head>
<meta charset="utf-8">
<title>KORVANEX Business Card</title>
<link rel="stylesheet" href="https://fonts.googleapis.com/css2?family=Play:wght@400;700&family=Roboto+Condensed:wght@300;400&display=swap">
<style>
  :root {
    --page-bg: #d9dbdc;
    --card-frost: #eef0f1;
    --card-edge: #c9cdd0;
    --brand-blue: #24477c;
    --brand-blue-deep: #1b3765;
    --brand-white: #f4f1ef;
    --name-blue: #3b5f93;
    --ink: #3a3d41;
    --icon: #4d6d98;
  }
  * { box-sizing: border-box; margin: 0; padding: 0; }
  html, body {
    width: 1200px; height: 952px; overflow: hidden;
    background: var(--page-bg);
    font-family: "Play", "Roboto Condensed", sans-serif;
  }
  .sheet {
    position: relative; width: 1200px; height: 952px;
  }
  .card {
    position: absolute; left: 250px;
    width: 700px; height: 400px;
    background: var(--card-frost);
    border: 1px solid var(--card-edge);
    border-radius: 6px;
    overflow: hidden;
    box-shadow: 0 10px 28px rgba(0,0,0,.12);
  }
  .card--back { top: 50px; }
  .card--front { top: 500px; }

  .brand-band {
    position: absolute; top: 0; bottom: 0;
    width: 265px;
    background: linear-gradient(160deg, var(--brand-blue) 0%, var(--brand-blue-deep) 100%);
    color: var(--brand-white);
  }
  .card--front .brand-band { left: 38px; }
  .card--back .brand-band { right: 40px; width: 300px; }

  .brand-mark {
    display: flex; flex-direction: column; align-items: center; gap: 14px;
  }
  .brand-mark__dot {
    width: 58px; height: 58px; border-radius: 50%;
    background: var(--brand-white);
  }
  .brand-mark__name {
    font-family: "Play", sans-serif; font-weight: 700;
    font-size: 34px; letter-spacing: 1px; color: var(--brand-white);
  }
  .card--front .brand-mark { margin-top: 70px; }
  .card--back .brand-mark { margin-top: 32px; }
  .card--back .brand-mark__dot { width: 44px; height: 44px; }
  .card--back .brand-mark__name { font-size: 24px; }

  .tagline {
    position: absolute; left: 0; right: 0; bottom: 34px;
    text-align: center;
    font-family: "Roboto Condensed", sans-serif; font-weight: 300;
    font-size: 21px; line-height: 1.4; letter-spacing: .5px;
    text-transform: uppercase;
  }

  .mission {
    position: absolute; left: 26px; right: 22px; top: 148px;
    font-family: "Play", sans-serif; font-size: 16.5px; line-height: 1.32;
    color: var(--brand-white);
  }

  .contact {
    position: absolute; left: 340px; top: 68px; right: 20px;
    color: var(--ink);
  }
  .contact__name {
    font-family: "Play", sans-serif; font-weight: 400;
    font-size: 24px; color: var(--name-blue); letter-spacing: .5px;
  }
  .contact__role { font-size: 15px; margin-top: 4px; }
  .contact__list { list-style: none; margin-top: 54px; }
  .contact__list li {
    display: flex; align-items: center; gap: 14px;
    font-size: 16px; line-height: 24px;
  }
  .contact__list svg { width: 13px; height: 13px; flex: none; }
  .contact__address { margin-top: 46px; font-size: 16px; line-height: 22px; }
</style>
</head>
<body>
<main class="sheet">

  <section class="card card--back" aria-label="Card back with mission statement">
    <div class="brand-band">
      <div class="brand-mark">
        <span class="brand-mark__dot"></span>
        <span class="brand-mark__name">KORVANEX</span>
      </div>
      <p class="mission">KORVANEX is the leading building services innovator. By combining technology with functional toos that improve efficiency in the workplace, we provide unparalleled service in the industry. Developing lasting relationships with our clients and associates is the cornerstone of our success.</p>
    </div>
  </section>

  <section class="card card--front" aria-label="Card front with contact details">
    <div class="brand-band">
      <div class="brand-mark">
        <span class="brand-mark__dot"></span>
        <span class="brand-mark__name">KORVANEX</span>
      </div>
      <p class="tagline">Where Care Finds<br>Its Pulse</p>
    </div>

    <div class="contact">
      <h1 class="contact__name">MARISA DELCOURT</h1>
      <p class="contact__role">Project Manager</p>
      <ul class="contact__list">
        <li>
          <svg viewBox="0 0 13 13" aria-hidden="true"><rect x="1.5" y="0.5" width="10" height="12" rx="1.5" fill="none" stroke="var(--icon)"/><rect x="3.5" y="2.5" width="6" height="3" fill="var(--icon)"/><rect x="3.5" y="7" width="6" height="4" fill="var(--icon)" opacity=".6"/></svg>
          1(800) 555-0142
        </li>
        <li>
          <svg viewBox="0 0 13 13" aria-hidden="true"><rect x="0.5" y="2.5" width="12" height="8" fill="none" stroke="var(--icon)"/><path d="M0.5 2.5 L6.5 7.5 L12.5 2.5" fill="none" stroke="var(--icon)"/></svg>
          name@korvanex-demo.net
        </li>
        <li>
          <svg viewBox="0 0 13 13" aria-hidden="true"><circle cx="6.5" cy="6.5" r="6" fill="var(--icon)"/><path d="M6.5 1 V12 M1 6.5 H12" stroke="var(--card-frost)" stroke-width="1"/></svg>
          www.korvanex-demo.net
        </li>
      </ul>
      <p class="contact__address">1840 Alder Crest Blvd. Suite 210<br>San Diego, CA 92130</p>
    </div>
  </section>

</main>
</body>
</html>
```